Custom Cabinet Shop Needs a website design

Hi,
We need a website for a Custom Cabinet Shop and Cabinet parts manufacturing business.
The business has two sides to it. One side provides custom Kitchens, vanities, entertainment units, offices and what not to homeowners and contractors.
The 2nd side of the business provides built to order cabinet boxes and other parts required to put together a project to other cabinet shops, small contractors looking to install there own cabinets.
Website will need a Gallery to display work.
Color scheme to go well with logo.
current website is www.brambleoakcustomcabinets.com
being changed to www.brambleoak.ca
Logo Included in attached files.
Tagline "Joinery with Spirit"
Mission Statement "Our passion is to deliver inspired cabinetry solutions to suit all your needs, supported by our phenomenal star class customer service"
The website should convey quality and professionalism.
Thank you.
Homeowners/ Contractors
Entertainment

```html
<!DOCTYPE html>
<html lang="en">
<head>
<meta charset="utf-8">
<title>Bramble Oak Custom Cabinets</title>
<link rel="stylesheet" href="https://fonts.googleapis.com/css2?family=Lato:wght@300;400;700&display=swap">
<style>
:root{
  --orange:#e8411a;
  --black:#000;
  --ink:#111;
  --white:#fff;
  --footer:#1e1e1e;
  --muted:#cfcfcf;
  --panel-text:#444;
}
*{margin:0;padding:0;box-sizing:border-box}
html,body{width:1200px;height:2936px;overflow:hidden;background:var(--black)}
body{position:relative;font-family:'Lato',sans-serif;color:var(--white)}
.abs{position:absolute}

/* header */
.site-header{left:0;top:0;width:1200px;height:122px;background:var(--black)}
.brand{left:113px;top:36px;display:flex;align-items:center;gap:12px}
.brand-mark{width:40px;height:40px;background:var(--orange)}
.brand-name{font-size:27px;font-weight:700;letter-spacing:1px;color:var(--white);line-height:1}
.main-nav{left:0;top:58px;width:1200px;font-size:15px}
.main-nav a{position:absolute;color:var(--white);text-decoration:none;white-space:nowrap}
.main-nav a.active{color:var(--orange)}
.search-btn{left:1057px;top:53px;width:29px;height:29px;background:var(--orange);border-radius:4px;display:flex;align-items:center;justify-content:center}

/* hero */
.hero{left:0;top:122px;width:1200px;height:588px;background:linear-gradient(100deg,#1d2230 0%,#3a2f28 40%,#5a4636 65%,#2a2420 100%)}
.hero-badge{left:112px;top:352px;width:391px;height:171px;background:var(--orange);border-radius:0 0 34px 0;padding:28px 0 0 22px}
.hero-badge p{font-size:50px;line-height:52px;font-weight:400;color:var(--white);letter-spacing:-0.5px}
.hero-dots{left:577px;top:640px;display:flex;gap:8px}
.hero-dots span{width:10px;height:10px;border-radius:50%;background:var(--white)}
.hero-dots span.on{background:var(--orange)}

/* welcome */
.welcome{left:0;top:710px;width:1200px;height:691px;background:var(--black)}
.welcome-title{left:0;top:762px;width:1200px;text-align:center;font-size:30px;font-weight:300;color:var(--orange)}
.mission{left:127px;top:828px;width:946px;text-align:center;font-size:19px;font-weight:300;line-height:32px}
.segment-tab{height:76px;padding:14px 0 0 22px;font-size:40px;font-weight:400;border-radius:0 40px 0 0}
.segment-card{border:7px solid;border-radius:0 0 20px 20px;height:316px;padding:0}
.segment-card .photo{width:100%;height:100%;border-radius:0 0 12px 12px}
.tab-res{left:112px;top:953px;width:262px;background:var(--orange);color:var(--white)}
.card-res{left:112px;top:1027px;width:473px;border-color:var(--orange);border-radius:0 20px 20px 20px}
.card-res .photo{background:linear-gradient(160deg,#d8d4cc,#8c8478 60%,#3b332c);border-radius:0 14px 14px 14px}
.tab-bus{left:613px;top:953px;width:262px;background:var(--white);color:var(--ink)}
.card-bus{left:613px;top:1027px;width:473px;border-color:var(--white);border-radius:0 20px 20px 20px}
.card-bus .photo{background:linear-gradient(160deg,#5b6f8c,#3a4a63 55%,#1c2230);border-radius:0 14px 14px 14px}

/* our work */
.our-work{left:0;top:1401px;width:1200px;height:1124px;background:radial-gradient(ellipse at 50% 40%,#3a3836 0%,#1f1e1d 60%,#0d0d0d 100%)}
.work-title{left:0;top:1468px;width:1200px;text-align:center;font-size:30px;font-weight:400}
.feature{left:112px;top:1554px;width:974px;height:395px;background:var(--white);box-shadow:0 6px 20px rgba(0,0,0,.6)}
.feature-photo{left:0;top:0;width:585px;height:395px;background:linear-gradient(180deg,#b9ab98 0%,#8b7a66 55%,#4a2318 75%,#3a1a12 100%)}
.feature-body{left:615px;top:0;width:340px;height:395px;color:var(--panel-text)}
.project-label{left:0;top:44px;font-size:26px;font-weight:400}
.arrows{left:258px;top:46px;display:flex;gap:14px}
.arrows span{width:30px;height:30px;border-radius:50%;background:#555;display:flex;align-items:center;justify-content:center}
.feature-name{left:0;top:100px;font-size:46px;font-weight:400;color:var(--orange);line-height:1}
.feature-sub{left:0;top:148px;font-size:30px;font-weight:400;line-height:1}
.feature-text{left:0;top:212px;width:335px;font-size:13px;line-height:25.5px}
.btn-orange{left:0;top:329px;width:125px;height:37px;background:var(--orange);color:var(--white);font-size:14px;border-radius:0 18px 0 18px;display:flex;align-items:center;justify-content:center}

.tile{width:307px;height:209px;background:var(--orange);overflow:hidden}
.tile .photo{height:150px;width:100%}
.tile .label{position:absolute;left:20px;bottom:20px;font-size:13px;color:var(--white)}
.tile .details{position:absolute;right:6px;bottom:6px;width:130px;height:42px;background:var(--black);color:var(--white);font-size:14px;border-radius:0 20px 0 20px;display:flex;align-items:center;justify-content:center}

/* footer */
.site-footer{left:0;top:2525px;width:1200px;height:411px;background:var(--footer)}
.footer-head{top:2568px;font-size:19px;color:var(--orange);font-weight:400}
.footer-list{list-style:none;font-size:15px;color:var(--white)}
.footer-list li{height:31px}
.contact-line{left:585px;font-size:15px;line-height:26px}
.contact-icon{left:538px;width:14px;height:14px}
.phones{left:585px;top:2778px;font-size:20px;line-height:31px}
.social-row{left:861px;width:200px;font-size:15px;display:flex;justify-content:space-between;align-items:center}
.social-dot{width:12px;height:12px;border-radius:50%;background:var(--white)}
.copyright{left:0;top:2894px;width:1200px;text-align:center;font-size:14px}
</style>
</head>
<body>

<header class="site-header abs">
  <div class="brand abs"><span class="brand-mark"></span><span class="brand-name">BRAMBLE OAK</span></div>
  <nav class="main-nav abs">
    <a class="active" style="left:558px">HOME</a>
    <a style="left:638px">GALLERY</a>
    <a style="left:738px">SERVICES</a>
    <a style="left:832px">WARRANTY</a>
    <a style="left:947px">CONTACT</a>
  </nav>
  <div class="search-btn abs">
    <svg width="14" height="14" viewBox="0 0 14 14"><circle cx="6" cy="6" r="4" fill="none" stroke="#fff" stroke-width="2"/><line x1="9" y1="9" x2="13" y2="13" stroke="#fff" stroke-width="2"/></svg>
  </div>
</header>

<section class="hero abs" role="img" aria-label="Photo of a finished basement kitchen with dark cabinetry, live-edge bar counter and stools"></section>
<div class="hero-badge abs"><p>Joinery<br>with Spirit</p></div>
<div class="hero-dots abs"><span class="on"></span><span></span><span></span><span></span></div>

<section class="welcome abs"></section>
<h1 class="welcome-title abs">WELCOME TO BRAMBLE OAK</h1>
<p class="mission abs">Our passion is to deliver inspired cabinetry solutions to suit all your needs, supported by our phenomenal star class customer service</p>

<div class="segment-tab tab-res abs">Residential</div>
<div class="segment-card card-res abs"><div class="photo" role="img" aria-label="Photo of a bright residential kitchen with white cabinets and an island"></div></div>
<div class="segment-tab tab-bus abs">Business</div>
<div class="segment-card card-bus abs"><div class="photo" role="img" aria-label="Photo of a built-in wall unit with open shelving and lower cabinets"></div></div>

<section class="our-work abs" role="img" aria-label="Dimmed background photo of a cabinetry interior"></section>
<h2 class="work-title abs">OUR WORK</h2>

<article class="feature abs">
  <div class="feature-photo abs" role="img" aria-label="Photo of a wood entertainment unit with a wall-mounted television and speakers"></div>
  <div class="feature-body abs">
    <div class="project-label abs">Project1</div>
    <div class="arrows abs">
      <span><svg width="12" height="12" viewBox="0 0 12 12"><path d="M8 1 3 6l5 5" fill="none" stroke="#fff" stroke-width="2.4"/></svg></span>
      <span><svg width="12" height="12" viewBox="0 0 12 12"><path d="M4 1l5 5-5 5" fill="none" stroke="#fff" stroke-width="2.4"/></svg></span>
    </div>
    <div class="feature-name abs">Bramble Oak</div>
    <div class="feature-sub abs">Custom Cabinets</div>
    <p class="feature-text abs">Lorem Ipsum is simply dummy text of the printing and typesetting industry. Lorem Ipsum has been the industry's standard dummy text ever since the 1500s, when an unknown printer...</p>
    <div class="btn-orange abs">View Details</div>
  </div>
</article>

<div class="tile abs" style="left:112px;top:2002px"><div class="photo" role="img" aria-label="Photo of a kitchen island with dark base cabinets" style="background:linear-gradient(160deg,#d6d2cb,#6b5a4a 60%,#241c16)"></div><span class="label">OUR WORK 2</span><span class="details">View Details</span></div>
<div class="tile abs" style="left:446px;top:2002px"><div class="photo" role="img" aria-label="Photo of tall dark wood shelving units" style="background:linear-gradient(160deg,#8b8378,#3a2d24 55%,#15100c)"></div><span class="label">OUR WORK 2</span><span class="details">View Details</span></div>
<div class="tile abs" style="left:779px;top:2002px"><div class="photo" role="img" aria-label="Photo of a dark kitchen with under-cabinet lighting" style="background:linear-gradient(160deg,#2e2620,#6b5036 55%,#1a1410)"></div><span class="label">OUR WORK 2</span><span class="details">View Details</span></div>
<div class="tile abs" style="left:112px;top:2241px"><div class="photo" role="img" aria-label="Photo of an open kitchen with a large island and pendant lights" style="background:linear-gradient(160deg,#c9b9a2,#6a5541 55%,#2a2019)"></div><span class="label">OUR WORK 2</span><span class="details">View Details</span></div>
<div class="tile abs" style="left:446px;top:2241px"><div class="photo" role="img" aria-label="Photo of a bright dining area with large windows" style="background:linear-gradient(160deg,#e4e2da,#b8ad98 55%,#7a6650)"></div><span class="label">OUR WORK 2</span><span class="details">View Details</span></div>
<div class="tile abs" style="left:779px;top:2241px"><div class="photo" role="img" aria-label="Photo of a bathroom vanity with a soaker tub" style="background:linear-gradient(160deg,#cdbb9a,#7c6550 55%,#2b1f18)"></div><span class="label">OUR WORK 2</span><span class="details">View Details</span></div>

<footer class="site-footer abs"></footer>
<h3 class="footer-head abs" style="left:113px">Quick Links</h3>
<h3 class="footer-head abs" style="left:327px">Support Links</h3>
<h3 class="footer-head abs" style="left:528px">Contact Us</h3>
<h3 class="footer-head abs" style="left:861px">Connect With Us</h3>

<ul class="footer-list abs" style="left:113px;top:2634px">
  <li>Home</li><li>Gallery</li><li>Services</li><li>Warranty</li><li>Contact</li>
</ul>
<ul class="footer-list abs" style="left:327px;top:2634px">
  <li>Privacy policy</li><li>Terms &amp; Conditions</li><li>Legal Notice</li>
</ul>

<svg class="contact-icon abs" style="top:2640px" viewBox="0 0 14 14"><rect x="2" y="0" width="10" height="14" rx="1" fill="#fff"/><rect x="4" y="3" width="6" height="1.5" fill="#1e1e1e"/><rect x="4" y="6" width="6" height="1.5" fill="#1e1e1e"/><rect x="4" y="9" width="6" height="1.5" fill="#1e1e1e"/></svg>
<p class="contact-line abs" style="top:2630px">48120 Cedar Line Road 17<br>Hollow Ridge, Alberta<br>T9Z 4K2</p>
<svg class="contact-icon abs" style="top:2740px" viewBox="0 0 14 14"><rect x="0" y="2" width="14" height="10" fill="#fff"/><path d="M0 2l7 6 7-6" fill="none" stroke="#1e1e1e" stroke-width="1.4"/></svg>
<p class="contact-line abs" style="top:2733px">Sales@brambleoakcustomcabinets.com</p>
<svg class="contact-icon abs" style="top:2786px" viewBox="0 0 14 14"><path d="M3 0l3 3-2 2c1 2 3 4 5 5l2-2 3 3-2 3C6 13 1 8 0 3z" fill="#fff"/></svg>
<p class="phones abs">403-555-0142<br>403-555-0187</p>

<div class="social-row abs" style="top:2634px"><span>Friendbook</span><span class="social-dot"></span></div>
<div class="social-row abs" style="top:2696px"><span>Chirper</span><span class="social-dot"></span></div>
<div class="social-row abs" style="top:2758px"><span>Circles Plus</span><span class="social-dot"></span></div>

<p class="copyright abs">© 2015 Compnay Name,All Rights Reserved</p>

</body>
</html>
```